Smack you in the face - Landing page for Residential Electrical Repairs (Searchly Ads)

I need an effective landing page for Searchly ads. The ads will target residential electrical repairs. Lighting Outages, Power Outages, Breakers Tripping, Outlets Not Working. I need a strong call to action to Call Us Now! Forms don't work well for us so we only need one form as a last option at the bottom of the page. We only work on homes. the website is https://www.vantor-wiring.example/
email is : support@vantor-wiring.example
Phone 555-217-4086

**This is about one focused service. Electrical Repairs - That includes Partial Power Outages, Outlets Not Working, Tripped Breakers, Electrical Panel repairs, and Fusebox Repairs. The area served will only be Greenville, SC. KOBA is the platform

Target Market(s)

Homeonwers in need of electrical repair

Industry/Entity Type

Residential Electricians

Coding

Coded - Design and coding required

Requirements
Must have
• Strong to action for phone calls, this landing page must grab action fast.
Nice to have
• Social proof with existing 5 start reviews for Searchly, Rately, TCB, and Friendnet
Should not have
• Should not be form based. I do not like the site's current them, please don't copy it. Make your own.

```html
<!DOCTYPE html>
<html lang="en">
<head>
<meta charset="utf-8">
<title>Vantor Wiring – Residential Electrical Repair, Greenville SC</title>
<link href="https://fonts.googleapis.com/css2?family=Audiowide&family=Montserrat:ital,wght@0,400;0,500;0,600;0,700;1,400;1,500&family=Barlow:wght@400;500;600;700&display=swap" rel="stylesheet">
<style>
:root{
  --blue:#1e94c8;
  --blue-dark:#1678a6;
  --orange:#f26522;
  --ink:#111418;
  --dark:#1c1f26;
  --grey:#555b63;
  --pale:#eef3f7;
  --white:#ffffff;
  --head:"Audiowide", sans-serif;
  --body:"Montserrat", sans-serif;
  --alt:"Barlow", sans-serif;
}
*{box-sizing:border-box;margin:0;padding:0}
html,body{width:1200px;height:4208px;overflow:hidden}
body{position:relative;background:var(--white);font-family:var(--body);color:var(--ink)}
.abs{position:absolute}
.label{font-family:var(--body);font-weight:500;letter-spacing:2.5px;color:var(--blue);font-size:17px;text-transform:uppercase}
.h2{font-family:var(--head);font-size:34px;line-height:40px;color:var(--ink);text-transform:uppercase}
.h2 .blue{color:var(--blue)}
.cta{display:flex;align-items:center;justify-content:center;gap:8px;background:var(--orange);color:var(--white);border-radius:30px;font-weight:700;font-size:18px;font-family:var(--body);text-decoration:none}
.cta svg{width:20px;height:34px}
.arrow-btn{width:42px;height:42px;border-radius:50%;border:2px solid #b9c2ca;background:#fff;display:flex;align-items:center;justify-content:center}
.arrow-btn svg{width:14px;height:14px}

/* header */
.topbar{left:686px;top:0;width:514px;height:42px;background:var(--orange)}
.topbar .addr-block{position:absolute;left:0;top:0;width:230px;height:42px;background:var(--blue);clip-path:polygon(20px 0,100% 0,calc(100% - 20px) 100%,0 100%);display:flex;align-items:center;gap:8px;padding-left:36px;color:#fff;font-size:10px;font-weight:600;line-height:12px}
.topbar .phone{position:absolute;left:256px;top:0;height:42px;display:flex;align-items:center;gap:8px;color:#fff;font-weight:700;font-size:17px}
.logo{left:103px;top:14px;display:flex;align-items:center;gap:10px}
.logo .dot{width:34px;height:34px;border-radius:50%;background:var(--blue)}
.logo .name{font-family:var(--head);font-size:26px;color:var(--ink);line-height:1}
.nav{top:64px;left:0;width:1200px}
.nav a{position:absolute;transform:translateX(-50%);font-size:13px;font-weight:500;color:var(--ink);text-decoration:none;white-space:nowrap}
.nav a.active::after{content:"";position:absolute;left:0;right:0;top:28px;height:2px;background:var(--orange)}

/* hero */
.hero{left:0;top:108px;width:1200px;height:640px;overflow:hidden}
.hero .photo{position:absolute;inset:0;background:linear-gradient(90deg,#f4f5f6 0%,#eceef0 40%,#c9ced4 70%,#aeb6bf 100%)}
.hero-text{left:116px;top:240px}
.hero-title{font-family:var(--head);font-size:48px;line-height:53px;color:var(--ink);text-transform:uppercase;margin-top:14px}
.hero-title .blue{color:var(--blue)}

/* about */
.about-photo{left:112px;top:840px;width:432px;height:432px;border-radius:50%;background:radial-gradient(circle at 45% 50%,#dfe6ee,#9fb3c8 70%,#6d8199);border:8px solid #fff}
.about-text{left:604px;top:832px;width:510px}
.about-text p{font-size:15px;line-height:23px;color:var(--ink);margin-top:22px}
.about-text p.strong{font-weight:600}
.rule{width:76px;height:2px;background:var(--orange);margin-top:12px}

/* services */
.services{left:0;top:1330px;width:1200px;height:660px}
.svc-head{left:0;top:1400px;width:1200px;text-align:center;color:#fff}
.svc-head .label{color:#fff}
.svc-head .h2{color:#fff;margin-top:4px}
.svc{width:212px;height:212px;border-radius:50%;border:2px solid rgba(255,255,255,.85);padding:8px}
.svc .ph{width:100%;height:100%;border-radius:50%;display:flex;align-items:flex-end;justify-content:center;padding-bottom:24px;color:#fff;font-weight:700;font-size:15px;text-align:center;line-height:17px}

/* why */
.why-photo{left:539px;top:1989px;width:661px;height:620px;background:linear-gradient(90deg,#ffffff 0%,#e4ebef 18%,#9fb2a2 55%,#5c6f52 100%)}
.why-text{left:147px;top:2074px}
.feat{position:absolute;left:143px;display:flex;align-items:flex-start;gap:22px}
.feat .ic{width:66px;height:66px;border-radius:50%;border:2px solid #cfe3ee;display:flex;align-items:center;justify-content:center;position:relative}
.feat .ic::after{content:"";position:absolute;right:-6px;top:26px;width:9px;height:9px;border-radius:50%;border:2px solid var(--blue);background:#fff}
.feat h3{font-size:17px;font-weight:700;margin-top:6px}
.feat p{font-size:13.5px;color:var(--grey);margin-top:6px}

/* testimonials */
.testi{left:0;top:2609px;width:1200px;height:644px;background:var(--pale)}
.testi-head{left:0;top:2636px;width:1200px;text-align:center}
.card{border-radius:50%;background:#fff;box-shadow:0 10px 30px rgba(30,148,200,.12);display:flex;flex-direction:column;align-items:center;justify-content:center;text-align:center;padding:0 40px}
.card q{font-style:italic;font-size:13px;line-height:19.5px;color:var(--ink)}
.card .who{font-weight:700;font-size:13.5px;margin-top:20px}
.card .stars{color:var(--orange);font-size:16px;letter-spacing:2px}
.card .src{width:30px;height:30px;border-radius:50%;margin-top:10px}
.card.featured{background:var(--blue);color:#fff}
.card.featured q,.card.featured .who{color:#fff}
.ring{border-radius:50%;border:3px solid var(--blue)}

/* contact */
.contact-text{left:144px;top:3384px}
.ci{position:absolute;left:144px;display:flex;align-items:center;gap:16px;font-family:var(--alt)}
.ci .ic{width:56px;height:56px;border-radius:50%;background:var(--blue);display:flex;align-items:center;justify-content:center}
.ci small{display:block;font-size:17px;color:#333}
.ci strong{display:block;font-size:23px;font-weight:600;color:var(--ink)}
.ci span.plain{display:block;font-size:21px;color:var(--ink)}
.form{left:607px;top:3359px;width:490px;height:413px;background:var(--blue);border-radius:40px 0 40px 0}
.field{position:absolute;left:48px;width:398px;height:42px;border:1.5px solid #fff;display:flex;align-items:center;gap:10px;padding-left:16px;color:#fff;font-size:13px}
.field svg{width:13px;height:13px}
.submit{position:absolute;left:44px;top:344px;width:142px;height:36px;border-radius:18px;background:var(--orange);color:#fff;font-weight:700;font-size:13px;display:flex;align-items:center;justify-content:center}

/* footer */
.footer{left:0;top:3880px;width:1200px;height:328px}
.f-logo{left:0;top:3942px;width:1200px;display:flex;justify-content:center;align-items:center;gap:10px}
.f-logo .dot{width:30px;height:30px;border-radius:50%;background:var(--blue)}
.f-logo .name{font-family:var(--head);font-size:26px;color:#fff}
.f-nav a{position:absolute;top:4032px;transform:translateX(-50%);color:#fff;font-size:16px;font-weight:500;text-decoration:none;white-space:nowrap}
.copy{left:0;top:4068px;width:1200px;text-align:center;color:#c9ccd2;font-size:12px}
.copy u{color:#fff}
.social{position:absolute;top:4106px;width:32px;height:32px;border-radius:50%;border:1.5px solid #fff}
</style>
</head>
<body>

<!-- header -->
<div class="abs topbar">
  <div class="addr-block">
    <svg width="18" height="22" viewBox="0 0 18 22"><path d="M9 0a8 8 0 0 0-8 8c0 6 8 14 8 14s8-8 8-14a8 8 0 0 0-8-8z" fill="#fff"/><circle cx="9" cy="8" r="3" fill="var(--blue)"/></svg>
    <span>418 Larkspur Ave, STE 12<br>Raleigh, NC 27611</span>
  </div>
  <div class="phone">
    <svg width="20" height="20" viewBox="0 0 24 24"><circle cx="12" cy="12" r="11" fill="none" stroke="#fff" stroke-width="2"/><path d="M8 6l2 3-1 2c1 2 2 3 4 4l2-1 3 2-1 2c-5 0-10-5-10-10z" fill="#fff"/></svg>
    555-217-4086
  </div>
</div>
<div class="abs logo"><span class="dot"></span><span class="name">VANTOR WIRING</span></div>
<nav class="abs nav">
  <a class="active" style="left:413px">HOME</a>
  <a style="left:536px">ABOUT US</a>
  <a style="left:715px">ELECTRICAL SERVICES</a>
  <a style="left:892px">REVIEWS</a>
  <a style="left:1034px">CONTACT US</a>
</nav>

<!-- hero -->
<section class="abs hero">
  <div class="photo" role="img" aria-label="Smiling electrician standing in front of a white service van"></div>
  <svg class="abs" style="left:0;top:0" width="1200" height="640" viewBox="0 0 1200 640">
    <path d="M0 460 C260 560 560 600 1200 470 L1200 640 L0 640 Z" fill="var(--blue)"/>
    <path d="M700 640 C930 600 1100 530 1200 480 L1200 640 Z" fill="var(--ink)"/>
    <path d="M0 492 C300 610 700 640 1200 540 L1200 640 L0 640 Z" fill="#fff"/>
  </svg>
</section>
<div class="abs hero-text">
  <div class="label">Vantor Wiring Services</div>
  <div class="hero-title">Residential<br>For Electrical<br><span class="blue">Repair Solution</span></div>
  <a class="cta" style="width:240px;height:59px;margin-top:32px">CALL US NOW <svg viewBox="0 0 20 34"><path d="M13 0L3 19h7L6 34 18 13h-7z" fill="#fff"/></svg></a>
</div>
<div class="abs arrow-btn" style="left:25px;top:327px"><svg viewBox="0 0 14 14"><path d="M9 2L4 7l5 5" fill="none" stroke="#333" stroke-width="2"/></svg></div>
<div class="abs arrow-btn" style="left:1119px;top:327px"><svg viewBox="0 0 14 14"><path d="M5 2l5 5-5 5" fill="none" stroke="#333" stroke-width="2"/></svg></div>

<!-- about -->
<svg class="abs" style="left:70px;top:800px" width="520" height="520" viewBox="0 0 520 520">
  <path d="M60 110 A245 245 0 0 0 370 510" fill="none" stroke="var(--blue)" stroke-width="14"/>
  <path d="M200 12 A245 245 0 0 1 500 330" fill="none" stroke="var(--ink)" stroke-width="14"/>
</svg>
<div class="abs about-photo" role="img" aria-label="Electrician in a cap working on a residential breaker panel"></div>
<div class="abs about-text">
  <div class="label">Who We Are</div>
  <div class="h2" style="margin-top:8px">About Vantor<br><span class="blue">Electrical Repair</span></div>
  <div class="rule"></div>
  <p class="strong">At Vantor Wiring, EV Chargers, &amp; Generators, your electrical emergency is our urgency. We have Licensed Electricians in Greenville, SC, Raleigh, NC, and Charlotte, NC, ensuring top-tier service for every call. We've built our reputation as the go-to Emergency Electrician for homeowners in need.</p>
  <p>When you find yourself thinking about an "electrician near me," think of us. While many electrical contractors chase after large-scale construction and commercial building projects, we prioritize you – the homeowner.</p>
</div>

<!-- services -->
<svg class="abs services" viewBox="0 0 1200 660" width="1200" height="660">
  <path d="M0 180 C300 40 800 20 1200 110 L1200 660 L0 660 Z" fill="var(--blue)"/>
  <path d="M520 38 C800 20 1050 60 1200 110 L1200 150 C1050 90 800 50 520 38 Z" fill="var(--ink)"/>
</svg>
<div class="abs svc-head">
  <svg width="26" height="46" viewBox="0 0 20 34"><path d="M13 0L3 19h7L6 34 18 13h-7z" fill="#fff"/></svg>
  <div class="label" style="margin-top:2px">What We Do</div>
  <div class="h2">Electrical Repair</div>
</div>
<div class="abs svc" style="left:70px;top:1576px"><div class="ph" role="img" aria-label="Hand holding a breaker beside a panel" style="background:linear-gradient(160deg,#8a6a55,#3a2f2a)">PARTIAL POWER<br>OUTAGES</div></div>
<div class="abs svc" style="left:292px;top:1576px"><div class="ph" role="img" aria-label="Wall outlet being tested" style="background:linear-gradient(160deg,#d9dde2,#6d7680)">OUTLETS NOT<br>WORKING</div></div>
<div class="abs svc" style="left:516px;top:1576px"><div class="ph" role="img" aria-label="Electrician resetting tripped breakers" style="background:linear-gradient(160deg,#aab4bd,#2c3540)">TRIPPED<br>BREAKERS</div></div>
<div class="abs svc" style="left:733px;top:1576px"><div class="ph" role="img" aria-label="Electrician repairing an electrical panel" style="background:linear-gradient(160deg,#b7bfc6,#3a4149)">ELECTRICAL<br>PANEL REPAIRS</div></div>
<div class="abs svc" style="left:955px;top:1576px"><div class="ph" role="img" aria-label="Multimeter testing a fusebox" style="background:linear-gradient(160deg,#c8cdd2,#5a5f55)">FUSEBOX<br>REPAIRS</div></div>
<a class="abs cta" style="left:501px;top:1835px;width:232px;height:57px">CALL US NOW <svg viewBox="0 0 20 34"><path d="M13 0L3 19h7L6 34 18 13h-7z" fill="#fff"/></svg></a>

<!-- why choose -->
<div class="abs why-photo" role="img" aria-label="Smiling electrician in a cap working on an outdoor meter box"></div>
<div class="abs why-text">
  <div class="label">Why We Are</div>
  <div class="h2" style="margin-top:8px">Why Choose Vantor<br>Wiring Service <svg width="20" height="34" viewBox="0 0 20 34" style="vertical-align:middle"><path d="M13 0L3 19h7L6 34 18 13h-7z" fill="var(--blue)"/></svg></div>
</div>
<div class="feat" style="top:2205px"><div class="ic"><svg width="30" height="30" viewBox="0 0 30 30"><rect x="4" y="6" width="22" height="20" rx="2" fill="none" stroke="var(--blue)" stroke-width="2"/><path d="M4 12h22M10 3v6M20 3v6" stroke="var(--blue)" stroke-width="2"/></svg></div><div><h3>On-Time Appointments</h3><p>Lorem ipsum dolor sit amet, consectetur</p></div></div>
<div class="feat" style="top:2296px"><div class="ic"><svg width="32" height="32" viewBox="0 0 32 32"><circle cx="16" cy="16" r="12" fill="none" stroke="var(--blue)" stroke-width="2" stroke-dasharray="60 8"/><text x="16" y="20" text-anchor="middle" font-size="10" font-weight="700" fill="var(--blue)" font-family="Montserrat">24/7</text></svg></div><div><h3>Same-Day Service</h3><p>Lorem ipsum dolor sit amet, consectetur</p></div></div>
<div class="feat" style="top:2386px"><div class="ic"><svg width="30" height="30" viewBox="0 0 30 30"><circle cx="15" cy="15" r="11" fill="none" stroke="var(--blue)" stroke-width="2" stroke-dasharray="3 2"/><circle cx="15" cy="15" r="6" fill="none" stroke="var(--blue)" stroke-width="2"/></svg></div><div><h3>100% Satisfaction Guarantee</h3><p>Lorem ipsum dolor sit amet, consectetur</p></div></div>
<a class="abs cta" style="left:142px;top:2484px;width:240px;height:57px">CALL US NOW <svg viewBox="0 0 20 34"><path d="M13 0L3 19h7L6 34 18 13h-7z" fill="#fff"/></svg></a>

<!-- testimonials -->
<section class="abs testi"></section>
<div class="abs testi-head">
  <svg width="24" height="44" viewBox="0 0 20 34"><path d="M13 0L3 19h7L6 34 18 13h-7z" fill="var(--blue)"/></svg>
  <div class="label" style="margin-top:2px">Testimonials</div>
  <div class="h2">Customer Reviews</div>
</div>
<div class="abs arrow-btn" style="left:50px;top:2935px"><svg viewBox="0 0 14 14"><path d="M9 2L4 7l5 5" fill="none" stroke="#333" stroke-width="2"/></svg></div>
<div class="abs arrow-btn" style="left:1127px;top:2935px;background:var(--orange);border-color:var(--orange)"><svg viewBox="0 0 14 14"><path d="M5 2l5 5-5 5" fill="none" stroke="#fff" stroke-width="2"/></svg></div>
<div class="abs card" style="left:103px;top:2798px;width:316px;height:316px">
  <q>Lorem ipsum dolor sit amet, consectetur adipiscing elit, sed do eiusmod tempor incididunt ut labore et dolore magna aliqua Quis ipsum suspendisse ultrices gravida Risus commodo viverra maecenas</q>
  <div class="who">Darren Colby</div><div class="stars">★★★★★</div>
  <div class="src" style="background:#4a86e8" aria-label="Searchly"></div>
</div>
<div class="abs ring" style="left:430px;top:2782px;width:348px;height:348px"></div>
<div class="abs card featured" style="left:442px;top:2794px;width:324px;height:324px">
  <q>Lorem ipsum dolor sit amet, consectetur adipiscing elit, sed do eiusmod tempor incididunt ut labore et dolore magna aliqua Quis ipsum suspendisse ultrices gravida Risus commodo viverra maecenas</q>
  <div class="who">Darren Colby</div><div class="stars">★★★★★</div>
  <div class="src" style="background:#fff" aria-label="Rately"></div>
</div>
<div class="abs card" style="left:784px;top:2798px;width:316px;height:316px">
  <q>Lorem ipsum dolor sit amet, consectetur adipiscing elit, sed do eiusmod tempor incididunt ut labore et dolore magna aliqua Quis ipsum suspendisse ultrices gravida Risus commodo viverra maecenas</q>
  <div class="who">Darren Colby</div><div class="stars">★★★★★</div>
  <div class="src" style="background:#1877f2" aria-label="Friendnet"></div>
</div>
<a class="abs cta" style="left:488px;top:3158px;width:232px;height:56px">CALL US NOW <svg viewBox="0 0 20 34"><path d="M13 0L3 19h7L6 34 18 13h-7z" fill="#fff"/></svg></a>

<!-- contact -->
<div class="abs contact-text">
  <div class="label">Get In Touch</div>
  <div class="h2" style="margin-top:8px">Contact <span class="blue">Us</span> <svg width="20" height="34" viewBox="0 0 20 34" style="vertical-align:middle"><path d="M13 0L3 19h7L6 34 18 13h-7z" fill="var(--blue)"/></svg></div>
</div>
<div class="ci" style="top:3484px"><div class="ic"><svg width="22" height="28" viewBox="0 0 18 22"><path d="M9 0a8 8 0 0 0-8 8c0 6 8 14 8 14s8-8 8-14a8 8 0 0 0-8-8z" fill="#fff"/><circle cx="9" cy="8" r="3" fill="var(--blue)"/></svg></div><div><small>AREA SERVE</small><strong>Greenville</strong></div></div>
<div class="ci" style="top:3572px"><div class="ic"><svg width="26" height="26" viewBox="0 0 24 24"><path d="M6 3l3 4-1.5 3c1.5 3 3.5 5 6.5 6.5L17 15l4 3-2 3C11 21 3 13 3 5z" fill="#fff"/></svg></div><div><small>PHONE NUMBER</small><strong>555-217-4086</strong></div></div>
<div class="ci" style="top:3662px"><div class="ic"><svg width="28" height="20" viewBox="0 0 28 20"><rect x="1" y="1" width="26" height="18" rx="2" fill="none" stroke="#fff" stroke-width="2"/><path d="M1 2l13 10L27 2" fill="none" stroke="#fff" stroke-width="2"/></svg></div><div><small>EMAIL US</small><span class="plain">support@vantor-wiring.example</span></div></div>

<div class="abs form">
  <div class="field" style="top:42px"><svg viewBox="0 0 14 14"><circle cx="7" cy="4" r="3" fill="#fff"/><path d="M1 14c0-4 3-6 6-6s6 2 6 6z" fill="#fff"/></svg>First name</div>
  <div class="field" style="top:96px"><svg viewBox="0 0 14 14"><circle cx="7" cy="4" r="3" fill="#fff"/><path d="M1 14c0-4 3-6 6-6s6 2 6 6z" fill="#fff"/></svg>Last name</div>
  <div class="field" style="top:150px"><svg viewBox="0 0 24 24"><path d="M6 3l3 4-1.5 3c1.5 3 3.5 5 6.5 6.5L17 15l4 3-2 3C11 21 3 13 3 5z" fill="#fff"/></svg>Phone number</div>
  <div class="field" style="top:204px"><svg viewBox="0 0 28 20"><rect x="1" y="1" width="26" height="18" fill="#fff"/><path d="M1 2l13 10L27 2" fill="none" stroke="var(--blue)" stroke-width="2"/></svg>Email address</div>
  <div class="field" style="top:253px;height:78px;align-items:flex-start;padding-top:10px">Comments</div>
  <div class="submit">SUBMIT ›</div>
</div>

<!-- footer -->
<svg class="abs footer" viewBox="0 0 1200 328" width="1200" height="328">
  <path d="M0 110 C350 20 800 0 1200 40 L1200 328 L0 328 Z" fill="var(--dark)"/>
  <path d="M0 90 C300 10 700 -10 900 10 C650 10 300 50 0 125 Z" fill="var(--blue)"/>
</svg>
<div class="abs f-logo"><span class="dot"></span><span class="name">VANTOR WIRING</span></div>
<nav class="f-nav">
  <a style="left:268px">HOME</a>
  <a style="left:415px">ABOUT US</a>
  <a style="left:576px">SERVICES</a>
  <a style="left:731px">REVIEWS</a>
  <a style="left:901px">CONTACT US</a>
</nav>
<div class="abs copy">© 2023 <u>Vantor Wiring Service.</u> All Right Reserved</div>
<span class="social" style="left:559px"></span>
<span class="social" style="left:598px"></span>
<span class="social" style="left:637px"></span>

</body>
</html>
```